Modern & Aesthetic Electrician Sign Design for Work Vehicle

Modern and aesthetic signage design for an electricians work vehicle. Including already designed logo, mobile number, ABN, licensing number and services offered. Preference is black background, symmetric design with logo centred, services offered at bottom of sign in smaller size font. Mobile number readable and big enough to standout without being too large.

Industry/Entity Type

Electrician

Font styles to use
Serif
Sans Serif

Colors
000000
ffffff
ec1f27

Requirements
Must have
• Logo
• Services Offered
• Mobile Number
• ABN
• License Number
• Black background

```html
<!DOCTYPE html>
<html lang="en">
<head>
<meta charset="utf-8">
<title>Kestrel Electrical – Vehicle Sign</title>
<link rel="stylesheet" href="https://fonts.googleapis.com/css2?family=Michroma&display=swap">
<style>
  :root {
    --black: #000000;
    --white: #ffffff;
    --red: #ec1f27;
    --charcoal: #3a3a3a;
    --backdrop: #f2f2f2;
  }
  * { margin: 0; padding: 0; box-sizing: border-box; }
  html, body {
    width: 1200px;
    height: 1000px;
    overflow: hidden;
    background: var(--backdrop);
  }
  .canvas {
    position: relative;
    width: 1200px;
    height: 1000px;
  }
  .vehicle-sign {
    position: absolute;
    left: 50px;
    top: 241px;
    width: 1100px;
    height: 518px;
    background: var(--black);
    overflow: hidden;
    font-family: "Michroma", sans-serif;
    color: var(--white);
  }
  .credentials {
    position: absolute;
    right: 30px;
    top: 28px;
    text-align: right;
    font-size: 12px;
    line-height: 20px;
    letter-spacing: 0.12em;
  }
  .brand {
    position: absolute;
    left: 0;
    top: 48px;
    width: 100%;
    display: flex;
    flex-direction: column;
    align-items: center;
  }
  .brand-ring {
    width: 160px;
    height: 160px;
    border: 12px solid var(--white);
    border-radius: 50%;
  }
  .brand-name {
    margin-top: 34px;
    font-size: 40px;
    line-height: 1;
    letter-spacing: 0.08em;
    color: var(--white);
  }
  .services {
    position: absolute;
    left: 0;
    top: 362px;
    width: 100%;
    text-align: center;
    font-size: 15px;
    line-height: 24px;
    letter-spacing: 0.14em;
    text-transform: uppercase;
  }
  .services .dot {
    display: inline-block;
    width: 8px;
    height: 8px;
    margin: 0 14px 2px;
    border-radius: 50%;
    background: var(--red);
    vertical-align: middle;
  }
  .footer-band {
    position: absolute;
    left: 0;
    bottom: 0;
    width: 1100px;
    height: 76px;
  }
  .phone {
    position: absolute;
    left: 0;
    bottom: 0;
    width: 900px;
    height: 76px;
    display: flex;
    align-items: center;
    justify-content: center;
    gap: 16px;
    padding-left: 60px;
    font-size: 38px;
    letter-spacing: 0.12em;
    color: var(--white);
  }
  .phone-icon { width: 40px; height: 40px; flex: none; }
</style>
</head>
<body>
<main class="canvas">
  <section class="vehicle-sign">
    <div class="credentials">
      <p>ABN 12 345 678 901</p>
      <p>LICENCE NO. 100234X</p>
    </div>

    <div class="brand">
      <div class="brand-ring"></div>
      <h1 class="brand-name">KESTREL ELECTRICAL</h1>
    </div>

    <div class="services">
      <p>Lighting &amp; Power<span class="dot"></span>Data &amp; Communications<span class="dot"></span>Audio Visual &amp; TV<span class="dot"></span>Security</p>
      <p>Automation<span class="dot"></span>Emergency Call Out Service<span class="dot"></span>Switchboard Upgrades</p>
    </div>

    <svg class="footer-band" viewBox="0 0 1100 76" aria-hidden="true">
      <polygon points="860,76 1100,6 1100,76" fill="var(--charcoal)"/>
      <polygon points="990,76 1100,38 1100,76" fill="var(--white)"/>
      <polygon points="0,0 900,0 945,30 830,76 0,76" fill="var(--red)"/>
    </svg>

    <div class="phone">
      <svg class="phone-icon" viewBox="0 0 40 40" aria-hidden="true">
        <circle cx="20" cy="20" r="19" fill="var(--white)"/>
        <path d="M14 10 l4 0 l2 6 l-3 2 a14 14 0 0 0 6 6 l2 -3 l6 2 l0 4 a3 3 0 0 1 -3 3 a20 20 0 0 1 -17 -17 a3 3 0 0 1 3 -3 z" fill="var(--red)"/>
      </svg>
      <span class="phone-number">0400 555 318</span>
    </div>
  </section>
</main>
</body>
</html>
```